Business card design for Automotive workshop

We need a business card for a new automotive repair and tyre shop called Keelstone Prime Automotive located in New Zealand. We are a clean, modern and fresh workshop and company.

Front needs to feature logo,
my name:
Marlo Fenwicke (director)

Address:
48 Tarn Lane
Whitianga 3510

Phone: 07 594 2713
Mobile: 027 451 9362
Email: office@keelstoneautomotive.example.nz
Website: keelstoneautomotive.example.nz

Back needs to feature an area to write down appointment details, date and time.

Also feature a list of jobs and work we do such as,
Vehicle Servicing
All Mechanical Repairs
Warrant of Fitness
Tyres & Wheel Alignments
Automotive Diagnostics
Automotive Parts & Supplies

```html
<!DOCTYPE html>
<html lang="en">
<head>
<meta charset="utf-8">
<title>Keelstone Prime Automotive – Business Card</title>
<link rel="stylesheet" href="https://fonts.googleapis.com/css2?family=Arimo:wght@400;700&family=Open+Sans:wght@400&family=Roboto:wght@500;700&display=swap">
<style>
  :root {
    --backdrop: #2b2b2b;
    --card: #ffffff;
    --brand-red: #e3202a;
    --ink: #1c1c1c;
    --rule: #8a8a8a;
    --rule-light: #c8c8c8;
    --list-ink: #3a3a3a;
  }
  * { margin: 0; padding: 0; box-sizing: border-box; }
  html, body {
    width: 1200px; height: 1108px; overflow: hidden;
    background: var(--backdrop);
  }
  .stage {
    position: relative; width: 1200px; height: 1108px;
    display: flex; justify-content: center; align-items: center; gap: 60px;
  }
  .card {
    width: 420px; height: 690px;
    background: var(--card);
    border-radius: 26px;
    box-shadow: 0 12px 30px rgba(0,0,0,0.45);
    display: flex; flex-direction: column; align-items: center;
    font-family: "Arimo", Arial, sans-serif;
    color: var(--ink);
  }

  /* Front */
  .card--front { padding-top: 150px; }
  .brand {
    display: flex; align-items: center; gap: 12px;
    color: var(--brand-red);
    font-family: "Roboto", Arial, sans-serif; font-weight: 700;
    text-transform: uppercase; letter-spacing: 1px;
  }
  .brand__mark { width: 22px; height: 22px; background: var(--brand-red); flex: none; }
  .brand__name { font-size: 24px; line-height: 1.15; text-align: left; }
  .person { margin-top: 86px; text-align: center; }
  .person__name {
    font-family: "Roboto", Arial, sans-serif; font-weight: 500;
    color: var(--brand-red); font-size: 27px; text-transform: uppercase;
  }
  .person__role { font-size: 18px; margin-top: 2px; }
  .icon-rule {
    display: flex; align-items: center; gap: 6px;
    width: 230px; margin-top: 10px;
  }
  .icon-rule::before, .icon-rule::after {
    content: ""; flex: 1; height: 1px; background: var(--rule);
  }
  .icon-rule svg { width: 22px; height: 22px; }
  .contact { margin-top: 14px; text-align: center; font-size: 19px; line-height: 1.25; }
  .divider { width: 230px; height: 1px; background: var(--rule); margin: 14px 0 12px; }
  .address { font-size: 19px; text-align: center; }

  /* Back */
  .card--back { padding: 150px 50px 0; align-items: stretch; }
  .appointment__title {
    font-family: "Roboto", Arial, sans-serif; font-weight: 500;
    color: var(--brand-red); font-size: 29px; text-transform: uppercase; text-align: center;
  }
  .field { display: flex; align-items: flex-end; gap: 14px; margin-top: 24px; font-size: 22px; }
  .field__line { flex: 1; height: 1px; background: var(--rule-light); margin-bottom: 2px; }
  .services { margin-top: 80px; }
  .services__title {
    display: flex; align-items: center; gap: 12px;
    font-family: "Roboto", Arial, sans-serif; font-weight: 500;
    color: var(--brand-red); font-size: 26px; text-transform: uppercase;
  }
  .services__title::before, .services__title::after {
    content: ""; flex: 1; height: 1px; background: var(--rule-light);
  }
  .services__list {
    list-style: none; margin-top: 6px; text-align: center;
    font-family: "Open Sans", Arial, sans-serif; font-size: 19px; line-height: 1.36;
    color: var(--list-ink);
  }
</style>
</head>
<body>
<main class="stage">
  <section class="card card--front" aria-label="Card front">
    <div class="brand">
      <span class="brand__mark"></span>
      <span class="brand__name">Keelstone Prime<br>Automotive</span>
    </div>

    <div class="person">
      <h1 class="person__name">Marlo Fenwicke</h1>
      <p class="person__role">Director</p>
    </div>

    <div class="icon-rule">
      <svg viewBox="0 0 22 22" aria-label="Phone"><rect width="22" height="22" rx="3" fill="var(--brand-red)"/><path d="M6 7c0-1 1-2 2-2h6c1 0 2 1 2 2v1h-3V7H9v1H6zM7 10h8l1 6H6z" fill="#fff"/></svg>
      <svg viewBox="0 0 22 22" aria-label="Mobile"><rect width="22" height="22" rx="3" fill="var(--brand-red)"/><rect x="7.5" y="4" width="7" height="14" rx="1.5" fill="#fff"/><rect x="9" y="6" width="4" height="9" fill="var(--brand-red)"/></svg>
      <svg viewBox="0 0 22 22" aria-label="Email"><rect width="22" height="22" rx="3" fill="var(--brand-red)"/><rect x="4" y="6" width="14" height="10" fill="#fff"/><path d="M4 6l7 6 7-6" fill="none" stroke="var(--brand-red)" stroke-width="1.4"/></svg>
      <svg viewBox="0 0 22 22" aria-label="Website"><rect width="22" height="22" rx="3" fill="var(--brand-red)"/><circle cx="11" cy="11" r="6.5" fill="none" stroke="#fff" stroke-width="1.6"/><path d="M4.5 11h13M11 4.5c-3 3.5-3 9.5 0 13M11 4.5c3 3.5 3 9.5 0 13" fill="none" stroke="#fff" stroke-width="1.2"/></svg>
    </div>

    <address class="contact" style="font-style:normal">
      07 594 2713<br>
      027 451 9362<br>
      office@keelstoneautomotive.example.nz<br>
      keelstoneautomotive.example.nz
    </address>
    <div class="divider"></div>
    <p class="address">48 Tarn Lane, Whitianga 3510</p>
  </section>

  <section class="card card--back" aria-label="Card back">
    <h2 class="appointment__title">Next Appointment</h2>
    <div class="field"><span>DATE</span><span class="field__line"></span></div>
    <div class="field"><span>TIME</span><span class="field__line"></span></div>

    <div class="services">
      <h2 class="services__title">Work We Do</h2>
      <ul class="services__list">
        <li>Vehicle Servicing</li>
        <li>All Mechanical Repairs</li>
        <li>Warrant of Fitness</li>
        <li>Tyres &amp; Wheel Alignments</li>
        <li>Automotive Diagnostics</li>
        <li>Automotive Parts &amp; Supplies</li>
      </ul>
    </div>
  </section>
</main>
</body>
</html>
```